RWT Fittings Ltd Business Cards

We need a business card with our business logo. We provide window and door installations on high-rises in west coast British Colombia, Canada.

I would like my business information and details on one side of the card, and the other side the company name with logo

Target Market(s)

General Contractors

Industry/Entity Type

Construction

Contact Information for Business Card

one side i want my company name and logo in the dark theme logo that i provided

Requirements
Must have
• Marco Peltieri, 16045518293, RWTFittings@mailbox-demo.com, 1407-5194 Linden Row Burnaby BC, V5H 2K9, Owner & Manager

```html
<!DOCTYPE html>
<html lang="en">
<head>
<meta charset="utf-8">
<title>RWT Fittings Ltd – Business Cards</title>
<link rel="stylesheet" href="https://fonts.googleapis.com/css2?family=Open+Sans:wght@400;600;700&display=swap">
<style>
  :root {
    --stage: #3a3a3a;
    --card-white: #ffffff;
    --card-black: #141414;
    --pattern-dark: #1e1e1e;
    --pattern-mid: #2b2b2b;
    --brand-blue: #29a8e0;
    --swoosh-grey: #9c9c9c;
    --ink: #2e2e2e;
  }
  * { margin: 0; padding: 0; box-sizing: border-box; }
  html, body {
    width: 1200px; height: 780px; overflow: hidden;
    background: var(--stage);
    font-family: "Open Sans", Arial, sans-serif;
  }
  .sheet {
    position: relative; width: 1200px; height: 780px;
    display: flex; align-items: center; justify-content: center; gap: 40px;
  }
  .card {
    position: relative; width: 540px; height: 310px; overflow: hidden;
    border-radius: 4px;
    box-shadow: 0 14px 30px rgba(0,0,0,.45);
  }

  /* Front: contact side */
  .card-front { background: var(--card-white); color: var(--ink); }
  .front-swoosh { position: absolute; inset: 0; width: 100%; height: 100%; }
  .holder { position: absolute; left: 34px; top: 58px; z-index: 1; }
  .holder-name {
    font-size: 21px; font-weight: 700; color: var(--brand-blue);
    text-transform: uppercase; letter-spacing: .2px; line-height: 1.1;
  }
  .holder-role { font-size: 13px; font-weight: 400; margin-top: 3px; }
  .contact-list { list-style: none; margin-top: 16px; font-size: 12.5px; line-height: 1.65; }
  .contact-list li { display: flex; align-items: center; gap: 7px; }
  .contact-icon { width: 11px; height: 11px; flex: none; fill: var(--brand-blue); }
  .address {
    position: absolute; right: 34px; bottom: 26px;
    font-size: 13.5px; line-height: 1.4; text-align: left; font-style: normal;
  }
  .wordmark {
    position: absolute; display: flex; align-items: center; gap: 9px;
    font-weight: 700; color: var(--brand-blue); white-space: nowrap;
  }
  .wordmark-square { width: 0.8em; height: 0.8em; background: var(--brand-blue); flex: none; }
  .card-front .wordmark { right: 30px; top: 172px; font-size: 26px; }

  /* Back: brand side */
  .card-back { background: var(--card-black); }
  .back-pattern {
    position: absolute; inset: 0;
    background: linear-gradient(135deg, var(--pattern-mid) 0%, var(--pattern-dark) 55%, var(--card-black) 100%);
  }
  .card-back .wordmark {
    left: 50%; top: 50%; transform: translate(-50%, -50%); font-size: 28px;
  }
</style>
</head>
<body>
<main class="sheet">

  <section class="card card-front" aria-label="Business card, contact side">
    <svg class="front-swoosh" viewBox="0 0 540 310" preserveAspectRatio="none" aria-hidden="true">
      <path d="M40 0 C230 12 410 55 540 135 L540 0 Z" fill="var(--brand-blue)"/>
      <path d="M34 0 C225 18 405 64 540 146 L540 140 C408 58 228 12 40 0 Z" fill="var(--swoosh-grey)"/>
    </svg>

    <div class="holder">
      <h1 class="holder-name">Marco Peltieri</h1>
      <p class="holder-role">Owner &amp; Manager</p>
      <ul class="contact-list">
        <li>
          <svg class="contact-icon" viewBox="0 0 24 24" aria-hidden="true"><path d="M6.6 10.8a15.1 15.1 0 0 0 6.6 6.6l2.2-2.2a1 1 0 0 1 1-.25 11.4 11.4 0 0 0 3.6.57 1 1 0 0 1 1 1V20a1 1 0 0 1-1 1A17 17 0 0 1 3 4a1 1 0 0 1 1-1h3.5a1 1 0 0 1 1 1c0 1.25.2 2.45.57 3.6a1 1 0 0 1-.25 1z"/></svg>
          16045518293
        </li>
        <li>
          <svg class="contact-icon" viewBox="0 0 24 24" aria-hidden="true"><path d="M2 5h20v14H2z M4 7v.5l8 5 8-5V7l-8 5z" fill-rule="evenodd"/></svg>
          RWTFittings@mailbox-demo.com
        </li>
        <li>
          <svg class="contact-icon" viewBox="0 0 24 24" aria-hidden="true"><circle cx="12" cy="12" r="10" fill="none" stroke="var(--brand-blue)" stroke-width="2.4"/><path d="M2 12h20M12 2c3 3 3 17 0 20M12 2c-3 3-3 17 0 20" fill="none" stroke="var(--brand-blue)" stroke-width="1.8"/></svg>
          www.rwtfittings-demo.com
        </li>
      </ul>
    </div>

    <div class="wordmark"><span class="wordmark-square"></span>RWT Fittings Ltd</div>

    <address class="address">1407-5194 Linden Row<br>Burnaby BC, V5H 2K9</address>
  </section>

  <section class="card card-back" aria-label="Business card, brand side">
    <div class="back-pattern" role="img" aria-label="Dark tonal repeating pattern of building shapes"></div>
    <div class="wordmark"><span class="wordmark-square"></span>RWT Fittings Ltd</div>
  </section>

</main>
</body>
</html>
```